Brightway Carpet and Tile cleaning Business card Design

I need a design that has the same feel as my van.
i would also like a prominent "Review us on facebook" somewhere, but not that it makes it look silly.
I would like the card to have a little bit of grey or black in the design as well.

It will need contact details
phone: 0455 817264
email: rkbrightwayclean@mailbox-example.com
website: www.brightwaycarpetandtilecleaning-example.com.au
facebook: /brightwaycarpetandtilecleaning

Industry/Entity Type

Business

Contact Information for Business Card

Phone number 0455817264
Email rkbrightwayclean@mailbox-example.com
Website www.brightwaycarpetandtilecleaning-example.com.au
Facebook/brightwaycarpetandtilecleaning

Colors
000000

Requirements
Must have
• Same feel as my van
• I want the card to stand out from the crowd
Nice to have
• Maybe include a tiny bit of a third colour? Grey's,blacks, orange?

```html
<!DOCTYPE html>
<html lang="en">
<head>
<meta charset="utf-8">
<title>Brightway Carpet and Tile cleaning – Business Card</title>
<link rel="stylesheet" href="https://fonts.googleapis.com/css2?family=Open+Sans:wght@400;700&display=swap">
<style>
  :root {
    --canvas-bg: #eceff1;
    --sky-light: #b4e8f6;
    --sky-mid: #4cc6ea;
    --sky-deep: #13addc;
    --paper: #ffffff;
    --paper-shade: #f1f1f1;
    --grass-light: #8cc962;
    --grass-deep: #4fae48;
    --ink: #1b1b1b;
    --logo-grey: #5c5f63;
    --logo-white: #ffffff;
  }
  * { box-sizing: border-box; margin: 0; padding: 0; }
  html, body {
    width: 1200px; height: 900px; overflow: hidden;
    background: var(--canvas-bg);
    font-family: "Open Sans", Arial, sans-serif;
  }
  .sheet {
    width: 1200px; height: 900px;
    display: flex; align-items: center; justify-content: center; gap: 40px;
  }
  .card {
    position: relative;
    width: 540px; height: 310px;
    overflow: hidden;
    box-shadow: 0 6px 18px rgba(0,0,0,.18);
  }

  /* Front face */
  .card-front {
    background: linear-gradient(180deg, var(--sky-light) 0%, var(--sky-mid) 55%, var(--sky-deep) 100%);
  }
  .card-front .bubble-field {
    position: absolute; left: 0; top: 0; width: 230px; height: 170px;
    background: radial-gradient(ellipse at 40% 50%, rgba(255,255,255,.22), rgba(255,255,255,0) 70%);
  }
  .card-front .brand {
    position: absolute; right: 42px; bottom: 52px;
    color: var(--logo-white);
    text-align: left;
  }

  /* Shared brand mark */
  .brand { display: flex; align-items: center; gap: 8px; }
  .brand-dot {
    width: 14px; height: 14px; border-radius: 50%;
    background: currentColor; flex: none;
  }
  .brand-name {
    font-weight: 700; font-size: 30px; line-height: 1;
    letter-spacing: -.5px;
  }
  .brand-tag {
    display: block; font-weight: 700; font-size: 11.5px;
    letter-spacing: 1.4px; text-transform: uppercase; margin-top: 4px;
  }

  /* Back face */
  .card-back {
    background: var(--paper);
    display: flex; flex-direction: column;
  }
  .card-back .head {
    height: 128px;
    background: linear-gradient(180deg, var(--paper) 0%, var(--paper-shade) 100%);
    display: flex; align-items: center; justify-content: center;
  }
  .card-back .brand { color: var(--logo-grey); }
  .card-back .band {
    position: relative; flex: 1;
    background: linear-gradient(180deg, var(--sky-mid) 0%, var(--sky-deep) 100%);
  }
  .card-back .band .bubble-field {
    position: absolute; left: 110px; top: 10px; width: 200px; height: 130px;
    background: radial-gradient(ellipse at 50% 50%, rgba(255,255,255,.18), rgba(255,255,255,0) 70%);
  }
  .card-back .grass {
    height: 42px;
    background: linear-gradient(180deg, var(--grass-light), var(--grass-deep));
  }
  .contact {
    position: absolute; right: 22px; top: 8px;
    list-style: none; text-align: center;
    color: var(--ink); font-size: 13.5px; line-height: 23px;
  }
  .contact .phone { font-size: 14px; }
</style>
</head>
<body>
<main class="sheet">

  <section class="card card-front" aria-label="Business card front">
    <div class="bubble-field" role="img" aria-label="Soft water bubbles decoration"></div>
    <div class="brand">
      <span class="brand-dot"></span>
      <div>
        <span class="brand-name">Brightway Clean</span>
        <span class="brand-tag">Carpet &amp; Tile Cleaning</span>
      </div>
    </div>
  </section>

  <section class="card card-back" aria-label="Business card back">
    <header class="head">
      <div class="brand">
        <span class="brand-dot"></span>
        <div>
          <span class="brand-name">Brightway Clean</span>
          <span class="brand-tag">Carpet &amp; Tile Cleaning</span>
        </div>
      </div>
    </header>
    <div class="band">
      <div class="bubble-field" role="img" aria-label="Soft water bubbles decoration"></div>
      <ul class="contact">
        <li class="phone">0455 817264</li>
        <li>rkbrightwayclean@mailbox-example.com</li>
        <li>www.brightwaycarpetandtilecleaning-example.com.au</li>
        <li>facebook /brightwaycarpetandtilecleaning</li>
      </ul>
    </div>
    <div class="grass"></div>
  </section>

</main>
</body>
</html>
```